creative brochure for lumawell advisory an innovative consulting company!

Im looking for a brochure to be designed. I am happy for the designer to be creative with it. Please use the colors from my logo and you can look at my website www.lumawelladvisory.example to get a feel. I will provide all the wording. Its aimed at small business owners and i want it to give off the vibe of professional and experienced.
The text logo and a photo of me is attached. Please edit the photo of me to make me look slimmer!
If you want to change text because you can make it sound better please go ahead. use my website to see if there is any other information in it that would make the brochure better or more credible/convincing.
I am open to ideas, lay out and how many pages it should be or if it should be double sided. I need one i can email and one i can print. Maybe use the sentence "Turn your business around now as the point which jumps out the most".
Updates

I have just uploaded a bigger version of the photo as requested. Please photoshop it to make me look thinner and perhaps crop it at the waist. Thanks

Hi everyone, great work so far. Im liking the designs. Maybe just a bit less color. you could use grey i guess or other plain colors. Im not a fan of the orange in my logo so just use it minimally in the next ones. Still considering the ones submitted though.

Hi everyone, please remove the words, jumps out as the main point and just have, turn your business around now.

Thanks

Could you please also include this email address in the contact details

maren.toovey@lumawelladvisory.example

Please change the words Turn your business around too unlock your business potential now.

Target Market(s)

Small business in australia

Industry/Entity Type

Small Business

Requirements
Must have
• as above, all that i have provided in the files must be used as a minimum
Nice to have
• great creative use of my brand colors
Should not have
• i dont want it to look to young or too over the top. I dont want any new colors.

```html
<!DOCTYPE html>
<html lang="en">
<head>
<meta charset="utf-8">
<title>Lumawell Advisory — Brochure Cover</title>
<link rel="stylesheet" href="https://fonts.googleapis.com/css2?family=Montserrat:wght@700;800;900&family=Cinzel:wght@500&display=swap">
<style>
  :root {
    --backdrop: #d9d9db;
    --page: #f2f2f3;
    --page-shade: #e3e3e5;
    --panel: #ffffff;
    --brand-blue: #2e86d6;
    --brand-orange: #f5a21a;
    --ink: #2b2b2b;
    --rule: #c9c9cc;
    --photo-light: #cfc6bb;
    --photo-dark: #2a2a2e;
  }
  * { box-sizing: border-box; margin: 0; padding: 0; }
  html, body { width: 1200px; height: 799px; overflow: hidden; }
  body {
    background: var(--backdrop);
    display: flex;
    align-items: center;
    justify-content: center;
  }
  .cover {
    position: relative;
    width: 540px;
    height: 763px;
    background: linear-gradient(160deg, var(--page) 0%, var(--page-shade) 100%);
    box-shadow: 0 10px 30px rgba(0,0,0,0.18);
    overflow: hidden;
  }
  .top-band {
    position: absolute;
    inset: 0 0 auto 0;
    height: 38px;
    display: flex;
    z-index: 3;
  }
  .top-band__orange { width: 34%; background: var(--brand-orange); }
  .top-band__blue {
    flex: 1;
    background: var(--brand-blue);
    color: #fff;
    font: 700 11px/38px "Montserrat", sans-serif;
    letter-spacing: 0.12em;
    text-transform: uppercase;
    padding-left: 18px;
  }
  .tagline-card {
    position: absolute;
    z-index: 2;
    top: 70px;
    right: 0;
    width: 330px;
    height: 170px;
    background: linear-gradient(180deg, #ffffff 0%, #ececee 100%);
    box-shadow: -4px 4px 14px rgba(0,0,0,0.10);
    padding: 24px 28px;
    text-align: right;
  }
  .tagline__lead {
    font: 900 17px/1.2 "Montserrat", sans-serif;
    color: var(--brand-orange);
    letter-spacing: 0.04em;
    text-transform: uppercase;
  }
  .tagline__now {
    font: 900 70px/1 "Montserrat", sans-serif;
    color: var(--brand-blue);
    margin-top: 18px;
    letter-spacing: 0.02em;
  }
  .portrait {
    position: absolute;
    z-index: 1;
    left: 0;
    top: 256px;
    width: 370px;
    height: 420px;
    background: linear-gradient(180deg, var(--photo-light) 0%, var(--photo-light) 35%, var(--photo-dark) 60%, var(--photo-dark) 100%);
  }
  .brand-panel {
    position: absolute;
    z-index: 2;
    left: 0; bottom: 0;
    width: 540px;
    height: 200px;
  }
  .brand-name {
    position: absolute;
    z-index: 3;
    right: 34px;
    bottom: 58px;
    display: flex;
    align-items: center;
    gap: 14px;
    font: 500 30px/1 "Cinzel", serif;
    color: var(--ink);
    text-transform: lowercase;
    white-space: nowrap;
  }
  .brand-name__mark {
    width: 22px; height: 22px;
    border-radius: 50%;
    background: var(--brand-blue);
  }
</style>
</head>
<body>
  <main class="cover">
    <div class="top-band">
      <div class="top-band__orange"></div>
      <div class="top-band__blue">Audit · Strategy · Growth</div>
    </div>

    <section class="tagline-card">
      <p class="tagline__lead">Unlock your business potential</p>
      <p class="tagline__now">NOW!!</p>
    </section>

    <div class="portrait" role="img" aria-label="Portrait of the consultant in a dark blazer and white blouse, arms folded, cropped at the waist"></div>

    <svg class="brand-panel" viewBox="0 0 540 200" aria-hidden="true">
      <path d="M0 90 C160 40 360 20 540 0 L540 200 L0 200 Z" fill="var(--panel)"/>
      <path d="M0 90 C160 40 360 20 540 0" fill="none" stroke="var(--rule)" stroke-width="2"/>
    </svg>

    <div class="brand-name">
      <span class="brand-name__mark"></span>
      <span>lumawell advisory</span>
    </div>
  </main>
</body>
</html>
```